Thornvale Agribusiness Consulting needs a Website Design.

We need a website design for a new company based in UK. Thornvale offers agribusiness consulting and farm design services to farmers, smallholders and the wider agribusiness industry to assist clients in adopting more sustainable and regenerative production, processing and marketing practices.
Services are offered face-to-face and on a remote platform.
Services are offered in the UK and overseas.
We would like to see designs that reflect the natural environment, business and sustainability. Desired colours; green, blue, grey. The final design should communicate professionalism in the rural economy.
The design should be able to be customized by the client to make future changes and additions.
Target Market(s)
Farmers, smallholders, and the agricultural industry in UK and overseas.
Industry/Entity Type
Agribusiness
Number of Pages Required
4 page
Look and feel
Each slider illustrates characteristics of the customer's brand and the style your logo design should communicate.

```html
<!DOCTYPE html>
<html lang="en">
<head>
<meta charset="utf-8">
<title>Thornvale Agribusiness Consulting</title>
<link href="https://fonts.googleapis.com/css2?family=Questrial&family=Open+Sans:wght@400;600;700&family=Oswald:wght@400&display=swap" rel="stylesheet">
<style>
  :root{
    --lime:#8dc63f;
    --teal:#1aa38a;
    --black:#000;
    --footer:#141414;
    --grey-bg:#f0f0f0;
    --text:#444;
    --white:#fff;
    --muted:#bbb;
  }
  *{margin:0;padding:0;box-sizing:border-box}
  html,body{width:831px;height:1200px;overflow:hidden;background:var(--white)}
  body{position:relative;font-family:"Open Sans",Arial,sans-serif;color:var(--text)}
  .abs{position:absolute}

  /* header */
  .site-header{left:0;top:0;width:831px;height:84px;background:var(--black)}
  .brand-block{left:0;top:0;width:240px;height:91px}
  .brand-name{left:0;top:36px;width:226px;text-align:center;font-family:"Questrial",sans-serif;font-weight:400;font-size:19px;color:var(--white);letter-spacing:.5px;display:flex;justify-content:center;align-items:center;gap:7px}
  .brand-dot{width:10px;height:10px;border-radius:50%;background:var(--white)}
  .main-nav{right:52px;top:33px;display:flex;gap:35px}
  .main-nav a{font-family:"Questrial",sans-serif;font-size:13px;font-weight:400;color:var(--white);text-decoration:none;letter-spacing:.2px;-webkit-text-stroke:.3px var(--white)}

  /* hero */
  .hero{left:0;top:84px;width:831px;height:382px;
    background:linear-gradient(180deg,#a8adb2 0%,#c6cacd 35%,#7f8a94 72%,#5f7a4a 80%,#6e9a3e 88%,#4f7f2b 100%)}

  .section-badge{width:48px;height:48px;border-radius:50%;background:var(--white);left:391px;display:flex;align-items:center;justify-content:center}
  .section-badge span{width:14px;height:14px;border-radius:50%;background:var(--lime)}

  /* welcome */
  .welcome-title{left:0;top:496px;width:831px;text-align:center;font-family:"Questrial",sans-serif;font-size:21px;color:#222}
  .welcome-title strong{color:var(--teal);font-weight:400;-webkit-text-stroke:.6px var(--teal);letter-spacing:.5px}
  .welcome-text{left:55px;top:532px;width:721px;text-align:center;font-size:10.4px;line-height:18px;color:#555}
  .btn-more{left:381px;top:620px;width:70px;height:22px;background:var(--teal);color:var(--white);border-radius:2px;font-family:"Questrial",sans-serif;font-size:9px;text-align:center;line-height:22px}

  /* what we do */
  .services{left:0;top:692px;width:831px;height:275px;background:var(--grey-bg)}
  .services-title{left:0;top:727px;width:831px;text-align:center;font-family:"Questrial",sans-serif;font-size:16px;color:#111;-webkit-text-stroke:.4px #111}
  .service{width:176px;height:176px;border-radius:50%;top:764px;overflow:hidden}
  .service-label{left:0;top:118px;width:176px;height:28px;background:rgba(255,255,255,.78);text-align:center;font-family:"Oswald",sans-serif;font-size:15px;line-height:28px;color:#111}
  .s-consult{left:78px;background:linear-gradient(180deg,#bcd7ee 0%,#9ec4e4 22%,#2e5a22 35%,#3f6a2c 55%,#7aa84a 75%,#8fc050 100%)}
  .s-produce{left:327px;background:radial-gradient(circle at 50% 50%,#f4f1ec 0%,#e9e6e1 55%,#cfcbc5 100%)}
  .s-market{left:576px;background:linear-gradient(135deg,#5b7a3a 0%,#b2452f 35%,#4c5a3c 60%,#d9b99a 100%)}

  /* footer */
  .site-footer{left:0;top:966px;width:831px;height:234px;background:var(--footer)}
  .f-head{top:990px;font-size:10.5px;font-weight:700;color:var(--white);text-transform:uppercase}
  .news-item{left:51px;width:168px}
  .news-date{font-size:7.5px;color:#777}
  .news-text{font-size:9.5px;line-height:13px;color:#ddd;margin-top:3px}
  .news-rule{left:51px;top:1061px;width:168px;height:1px;background:#333}
  .quick-links{left:238px;top:1010px;list-style:none}
  .quick-links li{font-size:9.5px;color:#ccc;line-height:18px}
  .contact-row{left:405px;display:flex;gap:10px;align-items:flex-start}
  .contact-icon{width:23px;height:23px;border-radius:50%;display:flex;align-items:center;justify-content:center;flex:none}
  .contact-text{font-size:9.5px;line-height:13px;color:#ccc}
  .contact-text .big{font-size:14px;color:var(--white);font-weight:600;line-height:18px}
  .news-intro{left:612px;top:1008px;width:170px;font-size:9.5px;line-height:13px;color:#ccc}
  .field{left:612px;width:168px;height:22px;background:var(--white);border-radius:2px;font-size:8px;color:#777;padding-left:7px;line-height:22px}
  .btn-subscribe{left:612px;top:1113px;width:168px;height:22px;background:var(--lime);border-radius:2px;color:var(--white);text-align:center;font-size:9.5px;font-weight:600;line-height:22px}
  .legal{left:51px;top:1164px;font-size:9px;color:#ccc}
  .legal span{margin:0 5px}
  .follow{left:700px;top:1162px;font-size:9px;color:#ccc;display:flex;align-items:center;gap:6px}
  .follow i{width:18px;height:18px;border-radius:50%;background:#2aa3e0;display:block}
</style>
</head>
<body>
  <header class="site-header abs"></header>
  <svg class="brand-block abs" viewBox="0 0 240 91" aria-hidden="true"><polygon points="0,0 237,0 220,91 0,91" fill="#8dc63f"/></svg>
  <div class="brand-name abs"><span class="brand-dot"></span>THORNVALE</div>
  <nav class="main-nav abs">
    <a href="#">HOME</a><a href="#">ABOUT US</a><a href="#">WHAT WE DO</a><a href="#">SERVICES</a><a href="#">CONTACT</a>
  </nav>

  <div class="hero abs" role="img" aria-label="Large oak tree standing alone in a green field under a cloudy grey sky"></div>

  <div class="section-badge abs" style="top:441px"><span></span></div>
  <h1 class="welcome-title abs">Welcome to <strong>THORNVALE</strong></h1>
  <p class="welcome-text abs">Nam liber tempor cum soluta nobis eleifend option congue nihil imperdiet doming id quod mazim placerat facer possim assum. Typi non habent claritatem insitam; est usus legentis in iis qui facit eorum claritatem. Claritas est etiam processus dynamicus, qui sequitur mutationem consuetudium lectorum. Mirum est notare quam littera gothica, quam nunc putamus parum claram, anteposuerit litterarum formas humanitatis per seacula quarta decima et quinta decima. Eodem modo typi, qui nunc nobis videntur parum clari, fiant sollemnes in futurum.</p>
  <div class="btn-more abs">LEARN MORE</div>

  <section class="services abs"></section>
  <div class="section-badge abs" style="top:668px;background:var(--grey-bg)"><span></span></div>
  <h2 class="services-title abs">WHAT WE DO</h2>
  <div class="service s-consult abs" role="img" aria-label="Herd of cattle grazing in a green pasture"><div class="service-label abs">CONSULTING</div></div>
  <div class="service s-produce abs" role="img" aria-label="Tray of white eggs with one brown egg"><div class="service-label abs">PRODUCTION</div></div>
  <div class="service s-market abs" role="img" aria-label="Crates of fresh local vegetables at a market stall"><div class="service-label abs">MARKETING</div></div>

  <footer class="site-footer abs"></footer>
  <div class="f-head abs" style="left:51px">Recent News</div>
  <div class="news-item abs" style="top:1008px"><div class="news-date">10 MAR 2015</div><div class="news-text">Mirum est notare quam littera gothi ca, quam nunc</div></div>
  <div class="news-rule abs"></div>
  <div class="news-item abs" style="top:1075px"><div class="news-date">10 MAR 2015</div><div class="news-text">Mirum est notare quam littera gothi ca, quam nunc</div></div>

  <div class="f-head abs" style="left:238px">Quick Links</div>
  <ul class="quick-links abs"><li>Home</li><li>About us</li><li>What we do</li><li>Services</li><li>Contact</li></ul>

  <div class="f-head abs" style="left:405px">Get in Touch</div>
  <div class="contact-row abs" style="top:1009px">
    <span class="contact-icon" style="background:var(--lime)"><svg width="10" height="12" viewBox="0 0 10 12"><path d="M5 0a4 4 0 0 1 4 4c0 3-4 8-4 8S1 7 1 4a4 4 0 0 1 4-4z" fill="#fff"/><circle cx="5" cy="4" r="1.5" fill="#8dc63f"/></svg></span>
    <div class="contact-text">228, Lorem ipsum dolor amet<br>sit aremt sor- 859584</div>
  </div>
  <div class="contact-row abs" style="top:1052px">
    <span class="contact-icon" style="background:var(--teal)"><svg width="11" height="11" viewBox="0 0 11 11"><path d="M2 0l2 2.5-1 1.2a7 7 0 0 0 4.3 4.3l1.2-1L11 9l-1.5 2C4.5 11 0 6.5 0 1.5z" fill="#fff"/></svg></span>
    <div class="contact-text">Phone :<br><span class="big">(+44) 01632 960418</span></div>
  </div>
  <div class="contact-row abs" style="top:1097px">
    <span class="contact-icon" style="background:#1f87c9"><svg width="11" height="8" viewBox="0 0 11 8"><rect width="11" height="8" rx="1" fill="#fff"/><path d="M0 0l5.5 4.5L11 0" stroke="#1f87c9" fill="none"/></svg></span>
    <div class="contact-text">Email :<br>info@thornvale-agri.com</div>
  </div>

  <div class="f-head abs" style="left:612px">Newsletter Signup</div>
  <p class="news-intro abs">Sign up to receive occasional e-mail updates about new features and special News from Thornvale.</p>
  <div class="field abs" style="top:1056px">Enter Your Name</div>
  <div class="field abs" style="top:1085px">Enter Your Email</div>
  <div class="btn-subscribe abs">SUBSCRIBE</div>

  <div class="legal abs">© 2015Thornvale. All Rights Reserved<span>•</span>Terms and Conditions<span>•</span>Privacy Policy<span>•</span>Terms of Use</div>
  <div class="follow abs">Follow Us On <i></i></div>
</body>
</html>
```